Website design for an Italian restaurant in Amsterdam

I need a design for a client of mine. It is for Teatro Lucerna, an Italian restaurant in Amsterdam.
We are going for a clean, modern look but we also need to realise an authentic feel.
The restaurant is located in an old movie theatre, that is where the name Teatro Lucerna comes from.
Industry/Entity Type
Italian Restaurant
Number of Pages Required
1 page
Font styles to use
Sans Serif
Colors
Designer to choose colors to be used in the design.

```html
<!DOCTYPE html>
<html lang="en">
<head>
<meta charset="utf-8">
<title>Teatro Lucerna – Italian Restaurant Amsterdam</title>
<link href="https://fonts.googleapis.com/css2?family=Lato:wght@400;700;900&family=Playfair+Display:wght@400;700&display=swap" rel="stylesheet">
<style>
:root{
  --crimson:#a3374a;
  --crimson-soft:#c14f63;
  --ink:#1b1b1b;
  --text:#3a3a3a;
  --white:#ffffff;
  --footer:#1f1f1f;
  --footer-text:#d8d8d8;
  --panel:rgba(255,255,255,0.86);
}
*{margin:0;padding:0;box-sizing:border-box}
html,body{width:1200px;height:2951px;overflow:hidden}
body{position:relative;font-family:"Lato",sans-serif;color:var(--text);background:var(--white)}
.abs{position:absolute}
.serif{font-family:"Playfair Display",serif}
.btn{position:absolute;display:flex;align-items:center;justify-content:center;background:var(--ink);color:var(--white);font-family:"Playfair Display",serif;font-weight:700;font-size:14px;letter-spacing:1px;text-transform:uppercase}

/* hero */
.hero{left:0;top:0;width:1200px;height:650px;background:radial-gradient(ellipse at 50% 18%,#6a5a3c 0%,#2b2622 35%,#141214 75%),#141214}
.hero-glow{left:0;top:0;width:1200px;height:650px;background:linear-gradient(90deg,rgba(60,50,140,.45) 0%,rgba(0,0,0,0) 30%,rgba(0,0,0,0) 70%,rgba(40,20,30,.3) 100%)}
.brand{left:78px;top:42px;display:flex;align-items:center;gap:10px;color:var(--white)}
.brand-dot{width:30px;height:30px;border-radius:50%;background:var(--crimson)}
.brand-name{font-family:"Playfair Display",serif;font-size:20px;letter-spacing:1px;text-transform:uppercase;line-height:1}
.brand-tag{font-size:9px;color:#bdbdbd;margin-top:3px;letter-spacing:.5px}
.topbar{right:78px;top:26px;display:flex;align-items:center;gap:36px;color:var(--white);font-family:"Playfair Display",serif;font-size:15px}
.flag{width:22px;height:14px;display:flex;flex-direction:column}
.flag i{flex:1}
.nav{right:78px;top:76px;display:flex;gap:42px;color:var(--white);font-family:"Playfair Display",serif;font-size:14px;text-transform:uppercase}
.hero-title{left:0;width:1200px;top:268px;text-align:center;color:var(--white);font-weight:900;font-size:66px;letter-spacing:2px}
.hero-sub{left:0;width:1200px;top:345px;text-align:center;color:var(--white);font-weight:700;font-size:30px}
.hero-btn{left:486px;top:412px;width:228px;height:40px;background:var(--crimson);font-size:16px}
.dots{left:566px;top:610px;display:flex;gap:9px}
.dots i{width:9px;height:9px;border-radius:50%;background:var(--white)}
.dots i:first-child{background:var(--crimson-soft)}

/* welcome */
.section-title{font-family:"Playfair Display",serif;color:var(--crimson);text-transform:uppercase;font-size:27px;text-align:center}
.welcome-title{left:0;width:1200px;top:718px}
.welcome-text{left:130px;width:940px;top:772px;text-align:center;font-size:14px;line-height:27px}
.welcome-btn{left:524px;top:882px;width:152px;height:41px}

/* feature rows */
.photo{position:absolute}
.panel{position:absolute;background:var(--panel);text-align:center}
.panel h2{font-family:"Playfair Display",serif;color:var(--crimson);font-weight:400;text-transform:uppercase;font-size:27px}
.panel p{font-size:14px;line-height:27px;margin:8px auto 0;width:330px;color:var(--text)}

/* contact */
.map{left:165px;top:2302px;width:871px;height:346px;background:linear-gradient(135deg,#c9cfd4,#dfe2e4 50%,#cfd6cf)}
.skyline{left:0;top:2560px;width:1200px;height:147px;background:linear-gradient(180deg,rgba(230,230,230,0),#ececec)}
.contact-card{left:345px;top:2335px;width:512px;height:285px;background:var(--white);text-align:center}
.contact-card h2{font-family:"Playfair Display",serif;color:var(--crimson);font-weight:400;text-transform:uppercase;font-size:27px;margin-top:44px}
.contact-name{font-weight:900;font-size:14px;color:var(--ink);text-transform:uppercase;margin-top:12px}
.contact-addr{font-size:14px;margin-top:4px}
.contact-line{display:flex;justify-content:center;align-items:center;gap:10px;font-size:14px;margin-top:10px}
.ic{color:var(--crimson)}

/* footer */
.footer{left:0;top:2707px;width:1200px;height:244px;background:var(--footer);color:var(--footer-text)}
.foot-brand{left:78px;top:70px}
.foot-copy{left:78px;top:130px;font-size:12px;line-height:22px}
.foot-col{top:48px;font-size:13px}
.foot-col h3{font-size:14px;font-weight:900;color:var(--white);text-transform:uppercase;margin-bottom:12px;letter-spacing:.5px}
.foot-col li{list-style:none;line-height:28px}
.hours{display:grid;grid-template-columns:100px auto;line-height:28px}
.subscribe{left:884px;top:82px;display:flex}
.subscribe span{width:200px;height:44px;background:var(--white);color:#777;font-size:13px;display:flex;align-items:center;padding-left:12px}
.subscribe b{width:44px;height:44px;background:var(--crimson);color:var(--white);display:flex;align-items:center;justify-content:center;font-size:14px}
.socials{left:884px;top:156px;display:flex;gap:14px}
.socials i{width:14px;height:14px;border-radius:50%;background:var(--white)}
</style>
</head>
<body>

<!-- hero -->
<div class="abs hero" role="img" aria-label="Dimly lit restaurant dining room with large circular chandeliers and a lit bar"></div>
<div class="abs hero-glow"></div>
<div class="abs brand">
  <div class="brand-dot"></div>
  <div><div class="brand-name">Teatro Lucerna</div><div class="brand-tag">Ristorante Italiano</div></div>
</div>
<div class="abs topbar">
  <span><span style="color:var(--crimson-soft)">&#9990;</span>&nbsp; (+31) 20 555 0142</span>
  <span class="flag"><i style="background:#ae1c28"></i><i style="background:#fff"></i><i style="background:#21468b"></i></span>
</div>
<nav class="abs nav"><span>Home</span><span>Menu (new)</span><span>Groupmenu</span><span>Reservation</span><span>Contact</span></nav>
<h1 class="abs hero-title">TEATRO LUCERNA</h1>
<div class="abs hero-sub">We are an Italian restaurant from Amsterdam</div>
<div class="btn hero-btn">Reserve a table</div>
<div class="abs dots"><i></i><i></i><i></i><i></i></div>

<!-- welcome -->
<h2 class="abs section-title welcome-title" style="font-weight:400">Welcome to Teatro Lucerna</h2>
<p class="abs welcome-text">Duis rhoncus pretium massa. Sed consequat in turpis non porta. Vivamus lobortis aliquam nulla venenatis porta. Proin id metus at massa iaculis elementum. Mauris nisi elit, gravida a pellentesque eget, sollicitudin a mi. &nbsp;In porttitor vel tellus et laoreet. Mauris imperdiet, magna eget sodales &nbsp;accumsan, tellus neque lacinia tellus, ac maximus turpis lorem sit amet urna.</p>
<div class="btn welcome-btn">Read more</div>

<!-- menu row -->
<div class="photo" style="left:0;top:1003px;width:1200px;height:415px;background:linear-gradient(90deg,#5a2a1a,#a0582e 35%,#6a3a22 58%,#c9c2b8 60%,#8a8580)" role="img" aria-label="Bruschetta with sun-dried tomatoes and basil"></div>
<div class="panel" style="left:704px;top:1003px;width:422px;height:415px;padding-top:118px">
  <h2>Menu</h2>
  <p>Duis rhoncus pretium massa. Sed consequat in turpis non porta. Vivamus lobortis aliquam nulla venenatis porta. Proin id metus at massa iaculis elementum.</p>
  <div class="btn" style="left:136px;top:264px;width:152px;height:41px">See menu</div>
</div>

<!-- groupmenu row -->
<div class="photo" style="left:0;top:1418px;width:1200px;height:414px;background:linear-gradient(90deg,#7a4a2a,#9a6a40 40%,#5a3020 60%,#8a5a3a)" role="img" aria-label="Antipasti platter with cheese, artichokes, breadsticks and a glass of red wine"></div>
<div class="panel" style="left:75px;top:1418px;width:420px;height:414px;padding-top:118px">
  <h2>Groupmenu</h2>
  <p>Duis rhoncus pretium massa. Sed consequat in turpis non porta. Vivamus lobortis aliquam nulla venenatis porta. Proin id metus at massa iaculis elementum.</p>
  <div class="btn" style="left:134px;top:264px;width:152px;height:41px">See groupmenu</div>
</div>

<!-- reservation row -->
<div class="photo" style="left:0;top:1832px;width:1200px;height:412px;background:linear-gradient(90deg,#3a1a14,#8a1e18 40%,#4a2018 60%,#5a2a20)" role="img" aria-label="Restaurant tables laid with red tablecloths and wine glasses"></div>
<div class="panel" style="left:704px;top:1832px;width:422px;height:412px;padding-top:118px">
  <h2>Reservation</h2>
  <p>Duis rhoncus pretium massa. Sed consequat in turpis non porta. Vivamus lobortis aliquam nulla venenatis porta. Proin id metus at massa iaculis elementum.</p>
  <div class="btn" style="left:116px;top:264px;width:190px;height:41px">Make reservation</div>
</div>

<!-- contact -->
<div class="abs skyline" role="img" aria-label="Faint Amsterdam skyline silhouette"></div>
<div class="abs map" role="img" aria-label="Street map around the restaurant location"></div>
<div class="abs contact-card">
  <h2>Contact us</h2>
  <div class="contact-name">Teatro Lucerna</div>
  <div class="contact-addr">Lindengracht 42 1015KB Amsterdam</div>
  <div class="contact-line">
    <span class="ic">&#9990;</span><span>(+31) 20 555 0142</span><span>|</span>
    <svg width="14" height="11" viewBox="0 0 14 11"><rect width="14" height="11" rx="1" fill="#a3374a"/><path d="M1 1l6 5 6-5" stroke="#fff" fill="none" stroke-width="1.3"/></svg>
    <span>info@teatrolucerna.nl</span>
  </div>
  <div class="btn" style="left:180px;top:216px;width:152px;height:41px">Contact us</div>
</div>

<!-- footer -->
<footer class="abs footer">
  <div class="abs brand foot-brand" style="top:68px">
    <div class="brand-dot"></div>
    <div class="brand-name">Teatro Lucerna</div>
  </div>
  <div class="abs foot-copy">© Copyright 2018 - Teatro Lucerna<br>All Right Reserved</div>
  <div class="abs foot-col" style="left:405px">
    <h3>Site menu</h3>
    <ul><li>Home</li><li>Menu (new)</li><li>Groupmenu</li><li>Reservation</li><li>Contact</li></ul>
  </div>
  <div class="abs foot-col" style="left:613px">
    <h3>Hours</h3>
    <div class="hours"><span>Tue - Sat</span><span>18:00 - 23:00</span><span>Sun &amp; Mon</span><b style="color:#fff">Closed</b></div>
  </div>
  <div class="abs foot-col" style="left:884px"><h3>Email subscribe</h3></div>
  <div class="abs subscribe"><span>Enter Email Address</span><b>GO</b></div>
  <div class="abs socials"><i></i><i></i><i></i><i></i><i></i><i></i><i></i></div>
</footer>

</body>
</html>
```